We need a logo for our business which is a dental clinic (i.e. dentistry).
We would lilke designs using the colour blue, green and black incorporating the words Corvath Dental, possibly a smile or a tooth image can be considered for incorporation in the logo.

Industry/Entity Type

Dental

```html
<!DOCTYPE html>
<html lang="en">
<head>
<meta charset="utf-8">
<title>Corvath Dental – Business Card</title>
<link rel="stylesheet" href="https://fonts.googleapis.com/css2?family=Exo+2:wght@500;600&display=swap">
<style>
  :root {
    --page-bg: #e4e7ec;
    --card-white: #f8f9fa;
    --card-white-shade: #e4e6e8;
    --aqua-light: #9adcf2;
    --aqua-mid: #5cc8e6;
    --aqua-deep: #22afd0;
    --leaf-green: #b2d75a;
    --brand-teal: #1f9fc4;
    --ink: #1c2630;
  }
  * { box-sizing: border-box; margin: 0; padding: 0; }
  html, body {
    width: 1200px;
    height: 840px;
    overflow: hidden;
    background: var(--page-bg);
    font-family: "Exo 2", sans-serif;
  }
  .business-card {
    position: absolute;
    left: 100px;
    top: 140px;
    width: 1000px;
    height: 560px;
    overflow: hidden;
    box-shadow: 0 10px 30px rgba(40, 60, 80, 0.18);
  }
  .card-artwork {
    position: absolute;
    inset: 0;
    width: 100%;
    height: 100%;
  }
  .brand-lockup {
    position: absolute;
    left: 64px;
    top: 222px;
    display: flex;
    align-items: center;
    gap: 16px;
  }
  .brand-mark {
    width: 40px;
    height: 40px;
    border-radius: 50%;
    background: var(--brand-teal);
    flex: none;
  }
  .brand-name {
    font-size: 42px;
    font-weight: 600;
    color: var(--brand-teal);
    letter-spacing: 0.5px;
    white-space: nowrap;
  }
  .contact-block {
    position: absolute;
    right: 36px;
    top: 58px;
    text-align: right;
    color: var(--ink);
  }
  .person-name {
    font-size: 22px;
    font-weight: 600;
    letter-spacing: 2px;
    text-transform: uppercase;
  }
  .person-role {
    font-size: 13px;
    font-weight: 500;
    letter-spacing: 1.5px;
    text-transform: uppercase;
    margin-top: 1px;
  }
  .postal-address {
    font-style: normal;
    font-size: 18px;
    font-weight: 500;
    line-height: 1.4;
    letter-spacing: 1px;
    margin-top: 46px;
  }
  .contact-list {
    list-style: none;
    margin-top: 38px;
  }
  .contact-item {
    display: flex;
    justify-content: flex-end;
    align-items: center;
    gap: 10px;
    font-size: 18px;
    font-weight: 500;
    letter-spacing: 1.5px;
    height: 32px;
    white-space: nowrap;
  }
  .contact-item.is-plain { font-size: 16px; letter-spacing: 0.8px; }
  .contact-icon {
    width: 18px;
    height: 18px;
    flex: none;
    fill: none;
    stroke: var(--ink);
    stroke-width: 1.8;
    stroke-linecap: round;
    stroke-linejoin: round;
  }
</style>
</head>
<body>
  <article class="business-card">
    <svg class="card-artwork" viewBox="0 0 1000 560" preserveAspectRatio="none" aria-hidden="true">
      <defs>
        <radialGradient id="aquaField" cx="0.72" cy="0.5" r="0.6">
          <stop offset="0" stop-color="var(--aqua-light)"/>
          <stop offset="0.55" stop-color="var(--aqua-mid)"/>
          <stop offset="1" stop-color="var(--aqua-deep)"/>
        </radialGradient>
        <radialGradient id="whiteField" cx="0.3" cy="0.35" r="0.8">
          <stop offset="0" stop-color="var(--card-white)"/>
          <stop offset="1" stop-color="var(--card-white-shade)"/>
        </radialGradient>
      </defs>
      <rect class="aqua-field" width="1000" height="560" fill="url(#aquaField)"/>
      <path class="leaf-sweep" d="M0,508 C470,492 748,310 782,0 L764,0 C728,298 458,478 0,494 Z" fill="var(--leaf-green)"/>
      <path class="white-field" d="M0,0 H760 C724,296 454,474 0,490 Z" fill="url(#whiteField)"/>
    </svg>

    <div class="brand-lockup">
      <span class="brand-mark" role="img" aria-label="Place for the Corvath Dental tooth mark"></span>
      <span class="brand-name">Corvath Dental</span>
    </div>

    <div class="contact-block">
      <h1 class="person-name">Dana Holloway</h1>
      <p class="person-role">President</p>
      <address class="postal-address">142.6th floor,Plaza<br>Harbour Street NVT</address>
      <ul class="contact-list">
        <li class="contact-item">013 482 7150
          <svg class="contact-icon" viewBox="0 0 24 24"><path d="M5 3h4l2 5-2.5 1.5a11 11 0 0 0 6 6L16 13l5 2v4a2 2 0 0 1-2 2A17 17 0 0 1 3 5a2 2 0 0 1 2-2z"/></svg>
        </li>
        <li class="contact-item">013 482 7150
          <svg class="contact-icon" viewBox="0 0 24 24"><rect x="7" y="2" width="10" height="20" rx="2"/><path d="M11 18h2"/></svg>
        </li>
        <li class="contact-item">013 482 7150
          <svg class="contact-icon" viewBox="0 0 24 24"><rect x="3" y="9" width="18" height="12" rx="1"/><path d="M7 9V3h8l2 2v4M7 13h2M11 13h2M15 13h2M7 17h2M11 17h2M15 17h2"/></svg>
        </li>
        <li class="contact-item">013 482 7150
          <svg class="contact-icon" viewBox="0 0 24 24"><rect x="3" y="5" width="18" height="14" rx="1"/><path d="M3 6l9 7 9-7"/></svg>
        </li>
        <li class="contact-item is-plain">hello@mailbox.com
          <svg class="contact-icon" viewBox="0 0 24 24"><circle cx="12" cy="12" r="9"/><path d="M3 12h18M12 3c3 3 3 15 0 18M12 3c-3 3-3 15 0 18"/></svg>
        </li>
        <li class="contact-item is-plain">www.corvathdental.com</li>
      </ul>
    </div>
  </article>
</body>
</html>
```